Business Card Design - VNT (company name)

Over 20 years of progressive technology design, migration and management experience that drives business objectives and streamlines operations. Continuously challenge conventions to meet and exceed business security, availability and functionality requirements. Maintain exceptional vendor relationships to ensure ongoing knowledge of emerging products and to secure preferred service agreements. Recruit and utilize top talent and foster a collegial environment that advances innovation and performance excellence. design logo using 3 arrows of different colors green, gold, blue

Industry/Entity Type

Progressive

Contact Information for Business Card

Martin K. Osgood
IT Strategist / Consultant

626.583.2907 MOsgood@vntosgood.example 4817 Brenning Court Pasadena, CA 91104

Colors
0255a3
f37122
fece3e

Requirements
Must have
• Note NEW EMAIL ADDRESS
• MOsgood@vntosgood.example
• NOTE NEW ORDER of the work I do.
• Infrastructure – Systems – Cybersecurity
Nice to have
• main color should be orange

```html
<!DOCTYPE html>
<html lang="en">
<head>
<meta charset="utf-8">
<title>VNT Business Card</title>
<link rel="stylesheet" href="https://fonts.googleapis.com/css2?family=Open+Sans:wght@400;600&display=swap">
<style>
  :root {
    --backdrop: #3a3633;
    --card: #151515;
    --card-edge: #0c0c0c;
    --text: #f2f2f2;
    --muted: #d8d8d8;
    --gold: #f8b928;
    --blue: #0a62e8;
    --orange: #f35a1e;
    --divider: #4a4a4a;
  }
  * { box-sizing: border-box; margin: 0; padding: 0; }
  html, body {
    width: 1200px; height: 844px; overflow: hidden;
    background: var(--backdrop);
    font-family: "Open Sans", Arial, sans-serif;
  }
  .stage {
    position: relative; width: 1200px; height: 844px;
    display: flex; align-items: center; justify-content: center; gap: 40px;
  }
  .card {
    position: relative; width: 540px; height: 309px;
    background: var(--card);
    box-shadow: 0 10px 28px rgba(0,0,0,.45);
    border-bottom: 3px solid var(--card-edge);
    color: var(--text);
  }
  .brand {
    position: absolute; left: 50%; transform: translateX(-50%);
    display: flex; align-items: center; gap: 12px;
  }
  .brand-dot {
    width: 22px; height: 22px; border-radius: 50%; background: var(--orange);
  }
  .brand-name {
    font-weight: 600; color: var(--orange); letter-spacing: 2px;
  }
  /* front */
  .card--front .brand { top: 58px; }
  .card--front .brand-name { font-size: 48px; }
  .identity {
    position: absolute; left: 36px; top: 172px; width: 230px;
  }
  .identity-name { font-size: 21px; font-weight: 400; line-height: 1.2; white-space: nowrap; }
  .identity-title { font-size: 14px; color: var(--gold); margin: 2px 0 10px; white-space: nowrap; }
  .identity-address { font-size: 13px; line-height: 1.45; color: var(--muted); }
  .divider {
    position: absolute; left: 274px; top: 170px; width: 1px; height: 100px;
    background: var(--divider);
  }
  .contacts {
    position: absolute; left: 290px; top: 182px; list-style: none;
  }
  .contacts li {
    display: flex; align-items: center; gap: 10px;
    font-size: 13px; margin-bottom: 10px; white-space: nowrap;
  }
  .contact-icon {
    width: 18px; height: 18px; background: var(--blue); border-radius: 2px;
    display: flex; align-items: center; justify-content: center; flex: none;
  }
  /* back */
  .card--back .brand { top: 88px; }
  .card--back .brand-name { font-size: 64px; }
  .card--back .brand-dot { width: 28px; height: 28px; }
  .services {
    position: absolute; left: 0; right: 0; bottom: 64px;
    text-align: center; font-size: 14px; letter-spacing: .2px;
  }
</style>
</head>
<body>
<main class="stage">
  <section class="card card--front">
    <div class="brand">
      <span class="brand-dot"></span>
      <span class="brand-name">VNT</span>
    </div>
    <div class="identity">
      <p class="identity-name">Martin K. Osgood</p>
      <p class="identity-title">IT Strategist / Consultant</p>
      <p class="identity-address">4817 Brenning Court<br>Pasadena, CA 91104</p>
    </div>
    <span class="divider"></span>
    <ul class="contacts">
      <li>
        <span class="contact-icon">
          <svg width="12" height="12" viewBox="0 0 12 12"><path d="M3 1h2l1 3-1.5 1a6 6 0 0 0 2.5 2.5L8 6l3 1v2a1 1 0 0 1-1 1A9 9 0 0 1 2 2a1 1 0 0 1 1-1z" fill="#fff"/></svg>
        </span>
        626.583.2907
      </li>
      <li>
        <span class="contact-icon">
          <svg width="12" height="12" viewBox="0 0 12 12"><rect x="1" y="3" width="10" height="7" fill="none" stroke="#fff" stroke-width="1.2"/><path d="M1 3l5 4 5-4" fill="none" stroke="#fff" stroke-width="1.2"/></svg>
        </span>
        MOsgood@vntosgood.example
      </li>
    </ul>
  </section>

  <section class="card card--back">
    <div class="brand">
      <span class="brand-dot"></span>
      <span class="brand-name">VNT</span>
    </div>
    <p class="services">Infrastructure | Systems | Cybersecurity</p>
  </section>
</main>
</body>
</html>
```